Corvane Capital Business Cards

These are professional business cards that are for my family office.
Put fake emails and phone numbers as of now until I finalize those components. This family office controls my families investments, assets, and future. The cards should be professional.
..
.
.
.
I just uploaded another variation of a logo I would like to see as a business card to I am inbeteen which logo to use

Target Market(s)

business

Industry/Entity Type

business

Contact Information for Business Card

Professional, wealth related, finance related.

Requirements
Must have
• Logo

```html
<!DOCTYPE html>
<html lang="en">
<head>
<meta charset="UTF-8">
<title>Corvane Capital Business Cards</title>
<link rel="stylesheet" href="https://fonts.googleapis.com/css2?family=Cinzel:wght@500;600;700&family=Arimo:wght@400&display=swap">
<style>
  :root {
    --navy: #1d2234;
    --white: #ffffff;
    --grey-band: #a9a8a8;
    --grey-light: #d9d9d9;
    --stage: #e6e6e8;
    --text-light: #f2f2f4;
  }
  * { margin: 0; padding: 0; box-sizing: border-box; }
  html, body {
    width: 1200px; height: 874px; overflow: hidden;
    background: var(--stage);
  }
  .canvas { position: relative; width: 1200px; height: 874px; }

  .card {
    position: absolute; left: 290px;
    width: 620px; height: 354px;
    border-radius: 26px; overflow: hidden;
  }

  /* Front */
  .card-front { top: 44px; background: var(--navy); }
  .front-mark {
    position: absolute; left: 50%; top: 80px;
    width: 120px; height: 120px; margin-left: -60px;
    border: 3px solid var(--white); border-radius: 50%;
  }
  .front-name {
    position: absolute; left: 0; right: 0; top: 222px;
    text-align: center;
    font-family: "Cinzel", serif; font-weight: 600;
    font-size: 30px; letter-spacing: 1px;
    color: var(--white);
  }

  /* Back */
  .card-back { top: 476px; background: var(--white); }
  .back-name {
    position: absolute; left: 0; right: 0; top: 98px;
    text-align: center;
    font-family: "Cinzel", serif; font-weight: 600;
    font-size: 46px; letter-spacing: 1px;
    color: var(--navy);
  }
  .back-band {
    position: absolute; left: 0; right: 0; top: 196px; height: 8px;
    background: var(--grey-band);
  }
  .back-panel {
    position: absolute; left: 0; right: 0; top: 204px; bottom: 0;
    background: var(--navy);
    color: var(--text-light);
    font-family: "Arimo", sans-serif;
  }
  .person {
    position: absolute; right: 338px; top: 28px;
    text-align: right; font-size: 15px; line-height: 19px;
  }
  .person-name {
    font-family: "Cinzel", serif; font-weight: 700;
    font-size: 22px; line-height: 26px; letter-spacing: 1px;
    margin-bottom: 2px;
  }
  .divider {
    position: absolute; left: 300px; top: 28px;
    width: 2px; height: 96px; background: var(--text-light);
  }
  .contacts {
    position: absolute; left: 314px; top: 44px;
    list-style: none; font-size: 15px; line-height: 19px;
  }
  .contacts li { display: flex; align-items: center; gap: 8px; }
  .contacts svg { width: 13px; height: 13px; flex: none; }
</style>
</head>
<body>
<main class="canvas">

  <section class="card card-front" aria-label="Card front">
    <div class="front-mark"></div>
    <div class="front-name">Corvane Capital</div>
  </section>

  <section class="card card-back" aria-label="Card back">
    <div class="back-name">Corvane Capital</div>
    <div class="back-band"></div>
    <div class="back-panel">
      <div class="person">
        <div class="person-name">Elias Marlowe</div>
        <div>President</div>
        <div>4120 Harbor Crest Way</div>
        <div>Whitby, Canada 58210</div>
      </div>
      <div class="divider"></div>
      <ul class="contacts">
        <li>
          <svg viewBox="0 0 16 16" aria-hidden="true"><path fill="#f2f2f4" d="M3.6 1.2l2.3 2.8-1.3 1.8c.9 2 2.6 3.7 4.6 4.6l1.8-1.3 2.8 2.3-1.4 2.2C7.2 15.2.8 8.8 1.4 2.6z"/></svg>
          555-210-4187
        </li>
        <li>
          <svg viewBox="0 0 16 16" aria-hidden="true"><rect x="4" y="1" width="8" height="14" rx="1.5" fill="none" stroke="#f2f2f4" stroke-width="1.6"/><circle cx="8" cy="12.5" r="0.9" fill="#f2f2f4"/></svg>
          555-392-7061
        </li>
        <li>
          <svg viewBox="0 0 16 16" aria-hidden="true"><rect x="1" y="3" width="14" height="10" fill="#f2f2f4"/><path d="M1 3l7 6 7-6" fill="none" stroke="#1d2234" stroke-width="1.4"/></svg>
          info@corvanecapital.com
        </li>
        <li>
          <svg viewBox="0 0 16 16" aria-hidden="true"><circle cx="8" cy="8" r="6.5" fill="none" stroke="#f2f2f4" stroke-width="1.5"/><path d="M1.5 8h13M8 1.5c-3 3.5-3 9.5 0 13M8 1.5c3 3.5 3 9.5 0 13" fill="none" stroke="#f2f2f4" stroke-width="1.2"/></svg>
          www.corvanecapital.com
        </li>
      </ul>
    </div>
  </section>

</main>
</body>
</html>
```